Brightway Haus Inc. Business Card Design

Brightway Haus Inc. is in search of a great clean design for our business cards!

Looking to incorporate our full logo and watermark on side one (however, I am open to having the text and watermark separated within the design.)

On side two, I am looking to have contact information (Name, Position, Phone #, Email, Website (www.thebrightwayhaus.ca). Can have the logo and/or watermark as part of the design if applicable.

Please add tagline "Where Shine Counts" on either side 1 or 2. This tagline can be in a sans serif, serif or cursive font as long as it compliments overall design. Capitalization can be title or sentence case depending on how it fits within the design.

Get creative!! Looking for a clean, crisp, premium design! Looking for a glossy card finish with spot UV features when printed. Cards will also be printed with rounded corners. Standard dimensions (3.5 x 2).

Target Market(s)

B2B - primary clients are business owners or property management corporations. (residential jobs are few and far between)

Industry/Entity Type

Business

Contact Information for Business Card

- clean, crisp design
- double sided
- spot UV accents and glossy finish upon printing
- standard business card size (3.5 x 2) with rounded corners
- please see project description for requirements per side

Font styles to use
Sans Serif

Requirements
Must have
• - adequate bleeds with print ready files
• - cohesive design elements between side 1 & 2
• - spot UV elements (can be on both sides or just one, use your discretion)
• - colour pallet should match the logo file provided
• - incorporate tagline "where shine counts" (this tagline can be in a serif or sans serif font as long as it is complimentary to the overall design.
Nice to have
• - Premium elements with a clean design
Should not have
• - Please omit cartoon or whimsical like designs, think premium.
• - Colours should not stray from the pallet of the provided logo.

```html
<!DOCTYPE html>
<html lang="en">
<head>
<meta charset="utf-8">
<title>Brightway Haus Inc. Business Card</title>
<link href="https://fonts.googleapis.com/css2?family=Roboto:ital,wght@0,400;0,500;0,700;1,400&display=swap" rel="stylesheet">
<style>
  :root {
    --stage: #2a2a2b;
    --navy: #1a2350;
    --teal: #12b1b4;
    --teal-card: #0fb2b4;
    --paper: #f3f3f3;
    --grey-stripe: #a9a9a9;
    --white: #ffffff;
  }
  * { margin: 0; padding: 0; box-sizing: border-box; }
  html, body {
    width: 1200px; height: 960px; overflow: hidden;
    background: var(--stage);
    font-family: "Roboto", Arial, sans-serif;
  }
  .card {
    position: absolute;
    width: 600px; height: 343px;
    border-radius: 22px;
    overflow: hidden;
  }
  .card-front { left: 314px; top: 113px; background: var(--paper); }
  .card-back { left: 311px; top: 472px; background: var(--teal-card); }
  .front-shape { position: absolute; inset: 0; }

  .holder { position: absolute; right: 36px; top: 40px; text-align: right; }
  .holder-name { color: var(--teal); font-size: 20px; font-weight: 500; letter-spacing: 0.3px; }
  .holder-role { color: var(--white); font-size: 14px; font-weight: 500; margin-top: 5px; }

  .address {
    position: absolute; right: 36px; top: 161px; text-align: right;
    color: var(--white); font-size: 14px; line-height: 18px;
  }
  .contacts { position: absolute; right: 36px; top: 208px; list-style: none; }
  .contacts li {
    display: flex; justify-content: flex-end; align-items: center; gap: 6px;
    color: var(--white); font-size: 14px; line-height: 19.5px;
  }
  .contacts svg { width: 13px; height: 13px; fill: var(--teal); }

  .brand { display: flex; align-items: center; gap: 8px; font-weight: 700; letter-spacing: -0.5px; }
  .brand-mark { display: block; }
  .brand-front { position: absolute; left: 36px; top: 228px; color: var(--navy); font-size: 27px; }
  .brand-front .brand-mark { width: 28px; height: 28px; background: var(--teal); }

  .brand-back {
    position: absolute; left: 0; right: 0; top: 142px; justify-content: center;
    color: var(--white); font-size: 40px;
  }
  .brand-back .brand-mark { width: 40px; height: 40px; background: var(--white); }

  .tagline {
    position: absolute; left: 110px; right: 110px; top: 276px;
    display: flex; align-items: center; gap: 4px;
    color: var(--white); font-size: 19px; font-style: italic; white-space: nowrap;
  }
  .tagline::before, .tagline::after {
    content: ""; flex: 1; height: 1px;
    background: linear-gradient(90deg, rgba(255,255,255,0), rgba(255,255,255,0.9));
  }
  .tagline::after { background: linear-gradient(90deg, rgba(255,255,255,0.9), rgba(255,255,255,0)); }
</style>
</head>
<body>
  <section class="card card-front">
    <svg class="front-shape" viewBox="0 0 600 343" aria-hidden="true">
      <path fill="var(--grey-stripe)" d="M263,0 C279,80 313,120 338,160 C366,205 356,282 310,322 C286,340 256,343 222,343 L600,343 L600,0 Z"/>
      <path fill="var(--teal)" d="M266,0 C282,80 318,120 345,160 C376,205 370,285 328,323 C303,342 266,343 230,343 L600,343 L600,0 Z"/>
      <path fill="var(--white)" d="M270,0 C286,80 322,120 352,160 C382,205 375,285 336,323 C312,342 280,343 248,343 L600,343 L600,0 Z"/>
      <path fill="var(--navy)" d="M272,0 C288,80 325,120 355,160 C385,205 378,285 340,323 C316,342 285,343 254,343 L600,343 L600,0 Z"/>
    </svg>

    <div class="brand brand-front"><span class="brand-mark"></span>BRIGHTWAY HAUS INC.</div>

    <div class="holder">
      <p class="holder-name">MAREN HOLT</p>
      <p class="holder-role">CEO/FOUNDER</p>
    </div>

    <p class="address">214 Larkspur Road<br>Kelowna, BC V1Y 2K9</p>

    <ul class="contacts">
      <li>250 555 0142 <svg viewBox="0 0 24 24"><path d="M6.6 10.8a15 15 0 006.6 6.6l2.2-2.2c.3-.3.7-.4 1-.2 1.1.4 2.3.6 3.6.6.6 0 1 .4 1 1V20c0 .6-.4 1-1 1A17 17 0 013 4c0-.6.4-1 1-1h3.5c.6 0 1 .4 1 1 0 1.3.2 2.5.6 3.6.1.3 0 .7-.2 1z"/></svg></li>
      <li>250 555 0187 <svg viewBox="0 0 24 24"><path d="M7 1h10a2 2 0 012 2v18a2 2 0 01-2 2H7a2 2 0 01-2-2V3a2 2 0 012-2zm0 3v14h10V4zm5 15.5a1 1 0 100 2 1 1 0 000-2z"/></svg></li>
      <li>250 555 0119 <svg viewBox="0 0 24 24"><path d="M6 2h12v5H6zM3 8h18a2 2 0 012 2v7h-4v5H5v-5H1v-7a2 2 0 012-2zm4 7v5h10v-5z"/></svg></li>
      <li>hello@brightwayhaus.ca <svg viewBox="0 0 24 24"><path d="M2 5h20v14H2zm2 2v.5l8 5 8-5V7l-8 5z"/></svg></li>
      <li>www.thebrightwayhaus.ca <svg viewBox="0 0 24 24"><circle cx="12" cy="12" r="10"/></svg></li>
    </ul>
  </section>

  <section class="card card-back">
    <div class="brand brand-back"><span class="brand-mark"></span>BRIGHTWAY HAUS INC.</div>
    <p class="tagline">Where Shine Counts</p>
  </section>
</body>
</html>
```